Upscale business cards needed for Board of Directors

We need professional business cards created for members of our family business Board of Directors. We would like these relatively simple and straightforward, but also with a unique element to set them apart. Probably stick with neutral and simple colors - white, grey etc. We need space for the traditional elements, including name, title, address, email/phone number. And we will be creating several from this template so it needs to be template that is easy to switch information in and out of.
Business
See description

```html
<!DOCTYPE html>
<html lang="en">
<head>
<meta charset="utf-8">
<title>Bramwell Holdings – Business Card</title>
<link href="https://fonts.googleapis.com/css2?family=Lato:wght@400;900&display=swap" rel="stylesheet">
<style>
  :root {
    --backdrop: #3a3a3a;
    --ink: #111111;
    --paper: #ffffff;
    --gold: #b19f75;
    --card-black: #050505;
  }
  * { box-sizing: border-box; margin: 0; padding: 0; }
  html, body {
    width: 1200px; height: 900px; overflow: hidden;
    background: var(--backdrop);
    font-family: "Lato", sans-serif;
  }
  .stage { position: relative; width: 1200px; height: 900px; }

  .card {
    position: absolute;
    width: 700px; height: 400px;
    box-shadow: 0 10px 30px rgba(0,0,0,0.45);
    overflow: hidden;
  }

  /* Back side */
  .card-back {
    left: 430px; top: 70px;
    background: var(--card-black);
    color: var(--paper);
  }
  .card-back .wordmark {
    position: absolute; left: 0; right: 0; top: 120px;
    text-align: center;
  }
  .card-back .website {
    position: absolute; left: 0; right: 0; bottom: 52px;
    text-align: center; font-size: 17px; letter-spacing: 2px;
  }

  .wordmark .main {
    display: block;
    font-weight: 900; font-size: 64px; line-height: 1; letter-spacing: 1px;
  }
  .wordmark .sub {
    display: block;
    font-weight: 900; font-size: 26px; letter-spacing: 14px; margin-top: 6px;
  }

  /* Front side */
  .card-front {
    left: 70px; top: 430px;
    background: var(--paper);
    color: var(--ink);
  }
  .card-front .swoosh { position: absolute; inset: 0; }
  .card-front .wordmark {
    position: absolute; left: 40px; top: 42px; color: var(--ink);
  }
  .card-front .wordmark .main { font-size: 54px; }
  .card-front .wordmark .sub { font-size: 22px; letter-spacing: 12px; padding-left: 4px; }

  .person { position: absolute; left: 40px; top: 170px; }
  .person .name { font-size: 25px; font-weight: 400; }
  .person .title { font-size: 17px; color: var(--gold); margin-top: 2px; }

  .address {
    position: absolute; left: 40px; top: 250px;
    font-size: 19px; line-height: 1.3;
  }

  .contacts {
    position: absolute; left: 300px; top: 268px;
    list-style: none; font-size: 19px; line-height: 1.25;
  }
  .contacts li { display: flex; align-items: center; gap: 12px; }
  .contacts svg { width: 16px; height: 16px; fill: var(--gold); flex: none; }
</style>
</head>
<body>
<main class="stage">

  <section class="card card-back" aria-label="Business card back">
    <div class="wordmark">
      <span class="main">BRAMWELL</span>
      <span class="sub">HOLDINGS</span>
    </div>
    <p class="website">www.bramwellholdings.com</p>
  </section>

  <section class="card card-front" aria-label="Business card front">
    <svg class="swoosh" viewBox="0 0 700 400" width="700" height="400" aria-hidden="true">
      <path d="M410,0 C610,65 678,235 680,400 L700,400 L700,0 Z" fill="var(--card-black)"/>
      <path d="M385,0 C575,55 640,225 640,400 L664,400 C664,230 600,60 398,0 Z" fill="var(--gold)"/>
    </svg>

    <div class="wordmark">
      <span class="main">BRAMWELL</span>
      <span class="sub">HOLDINGS</span>
    </div>

    <div class="person">
      <p class="name">Daniel Morrow</p>
      <p class="title">Director</p>
    </div>

    <address class="address" style="font-style:normal">
      1450 Cedar Lane<br>
      Linden TX 78020
    </address>

    <ul class="contacts">
      <li>
        <svg viewBox="0 0 16 16" aria-label="Phone"><path d="M3 1l3 0 1 4-2 1c1 2 2 3 4 4l1-2 4 1 0 3c0 1-1 2-2 2C6 14 2 10 1 3c0-1 1-2 2-2z"/></svg>
        512 555 0142
      </li>
      <li>
        <svg viewBox="0 0 16 16" aria-label="Fax"><rect x="4" y="1" width="8" height="4"/><rect x="1" y="6" width="14" height="6" rx="1"/><rect x="4" y="10" width="8" height="5" fill="#fff" stroke="var(--gold)" stroke-width="1.2"/></svg>
        512 555 0143
      </li>
      <li>
        <svg viewBox="0 0 16 16" aria-label="Email"><rect x="1" y="3" width="14" height="10" rx="1"/><path d="M1.5 3.5 8 9l6.5-5.5" fill="none" stroke="#fff" stroke-width="1.3"/></svg>
        info@bramwellholdings.com
      </li>
      <li>
        <svg viewBox="0 0 16 16" aria-label="Website"><circle cx="8" cy="8" r="7"/><path d="M1 8h14M8 1c-3 3-3 11 0 14M8 1c3 3 3 11 0 14" fill="none" stroke="#fff" stroke-width="1"/></svg>
        www.bramwellholdings.com
      </li>
    </ul>
  </section>

</main>
</body>
</html>
```